Need 8.5" x 11" as well as large 11"x17" Posters for our upcoming eventPlease include LOGOs in poster Main logo is Interfaith Youth Council of OCInfo/Content to include:All high school age faith groups are invited to come and join with 150 to 175 other high school students from various faith traditions to participate in the Crosspath Teen Assembly of Bramble Valley‘s Annual Crosspath Teen Gathering. More than ever, our county and the world needs young leaders who are willing to learn from each other and build stronger communities!FAITH FORUMThe purpose of this Crosspath Teen Gathering is to bring together young people from diverse ethnic, cultural, and religious backgrounds, and to engage them in dialogue. True dialogue is a conversation on a common subject between two or more persons of differing points of view and/or backgrounds. We feel that this commitment to dialogue will affect relationships in a constructive way in our places of worship and in our community.The forum itself involves having eight religiously diverse high school-age students, one adult, and youth leader around each table to discuss common questions. Our youth leaders act as facilitators, but it is stressed that it is the students we want to hear from.
Registration is Required for our UNITY SUMMIT before February 25th, 2019
FORUM QUESTIONS and rregistration available online at http://ctabv.example/home/unity-fair/

Target Market(s)

Houses of worship, community leaders, High School Students

Industry/Entity Type

Non-Profit

Font styles to use
Serif

Colors
fefcec
f78f20
faa54b
fece3e
3176b5
33a6d7
0592cd
0455a3
f68d4d

Requirements
Must have
• Must Have:
• - Crosspath Teen Assembly of Bramble Valley's 15th Annual Unity Summit & Fair
• - TEENS EXPRESSING THEIR FAITH THROUGH ART, MUSIC, AND DIALOGUE
• - THIS YEAR'S THEME: "Threads of Belief"
• - Sunday, March 10th, 2019 1:30pm-6:30pm
• - The Fellowship Hall of Saint Quillan Meadows
• - 4870 Larkspur Hollow Road Larkspur Falls, BV 00412
• - Email: ctabvgroup@mailbox.example
• - Website: CTABV.example
• - Facebook: Crosspath Teen Assembly of Bramble Valley
• Please include pictures provided
• Logo must be on there and prominent: Crosspath Teen assembly of Bramble Valley
• second logo should be somewhere on the bottom or back: Amberline Collective
Nice to have
• Descriptions provided in word doc
• Ideally would like Logo and pictures and main info on the front
• - Website: CTABV.example
• On the back have more details about the program and pics if needed

```html
<!DOCTYPE html>
<html lang="en">
<head>
<meta charset="utf-8">
<title>Crosspath Teen Assembly – Unity Summit &amp; Fair Flyer</title>
<link rel="stylesheet" href="https://fonts.googleapis.com/css2?family=Alfa+Slab+One&family=Barlow+Semi+Condensed:wght@400;500;600;700;800&family=Barlow:wght@400;500;600&display=swap">
<style>
  :root{
    --slate:#2e3537;
    --slate-deep:#262c2e;
    --teal:#4bb3c8;
    --teal-dark:#1f7088;
    --sky:#33a6d7;
    --brown:#7b4a1d;
    --ink:#2b2b2b;
    --paper:#ffffff;
    --mist:#eceef0;
    --stage:#e6e7e9;
  }
  *{box-sizing:border-box;margin:0;padding:0}
  html,body{width:1200px;height:776px;overflow:hidden}
  body{background:var(--stage);position:relative;font-family:"Barlow",sans-serif}
  .sheet{position:absolute;top:45px;width:530px;height:686px;overflow:hidden;box-shadow:0 4px 14px rgba(0,0,0,.18)}
  .sheet--front{left:50px;background:var(--paper)}
  .sheet--back{left:620px;background:linear-gradient(180deg,#f7f8f9 0%,var(--mist) 100%)}
  .abs{position:absolute}

  /* front */
  .header-band{left:0;top:12px;width:100%;height:32px;background:var(--teal);color:#fff;
    font-family:"Barlow Semi Condensed",sans-serif;font-weight:700;font-size:18px;letter-spacing:.4px;
    line-height:32px;padding-left:22px}
  .brand-mark{left:16px;top:54px;width:118px;height:118px;border:3px solid var(--ink);border-radius:50%;
    display:flex;align-items:center;justify-content:center;text-align:center;padding:12px;
    font-family:"Barlow Semi Condensed",sans-serif;font-weight:700;font-size:13px;line-height:1.15;color:var(--ink)}
  .title-block{left:150px;top:50px;width:372px;text-align:right;padding-right:8px}
  .title-annual{font-family:"Alfa Slab One",serif;font-size:44px;line-height:1;color:var(--teal-dark);text-align:left;padding-left:6px}
  .title-event{font-family:"Alfa Slab One",serif;font-size:21px;color:var(--brown);line-height:1.15;margin-top:4px}
  .title-tag{font-family:"Barlow Semi Condensed",sans-serif;font-size:16px;font-weight:500;color:var(--ink);letter-spacing:.3px;line-height:1.1}
  .title-media{font-family:"Alfa Slab One",serif;font-size:21px;color:var(--brown);line-height:1.15}

  .photo{background:linear-gradient(160deg,#8c6f61 0%,#5e4a45 45%,#9cb8c4 100%)}
  .photo-crowd{left:0;top:182px;width:100%;height:270px}
  .front-base{left:0;top:0;width:530px;height:686px}
  .photo-round{border:4px solid #fff;border-radius:50%;box-shadow:0 2px 6px rgba(0,0,0,.35)}
  .photo-round--a{left:70px;top:360px;width:116px;height:116px;background:linear-gradient(160deg,#b7c6cf,#6b5a4e)}
  .photo-round--b{left:190px;top:348px;width:116px;height:116px;background:linear-gradient(160deg,#c9c3d2,#8e7d80)}
  .photo-round--c{left:312px;top:336px;width:116px;height:116px;background:linear-gradient(160deg,#c74a3a,#e3b23c)}

  .theme{left:0;top:472px;width:100%;text-align:center;color:#fff;font-family:"Barlow Semi Condensed",sans-serif;font-weight:700;font-size:50px;letter-spacing:.3px}
  .date-row{left:60px;top:540px;height:36px;display:flex;align-items:center}
  .date-pill{background:#fff;color:var(--ink);border-radius:18px;height:34px;padding:0 22px;z-index:2;
    font-family:"Barlow Semi Condensed",sans-serif;font-weight:700;font-size:21px;line-height:34px}
  .time-pill{background:var(--teal);color:var(--slate);border-radius:0 18px 18px 0;height:34px;margin-left:-18px;padding:0 18px 0 30px;
    font-family:"Barlow Semi Condensed",sans-serif;font-weight:700;font-size:21px;line-height:34px}
  .venue{left:0;top:588px;width:100%;text-align:center;color:#fff;font-family:"Barlow Semi Condensed",sans-serif;font-weight:700;font-size:19px}
  .address{left:0;top:615px;width:100%;text-align:center;color:#fff;font-family:"Barlow Semi Condensed",sans-serif;font-weight:600;font-size:13px}
  .contact-box{left:26px;top:638px;width:478px;height:30px;border:2px solid #fff;display:flex;align-items:center;justify-content:center;gap:10px;padding:0 8px;
    color:#fff;font-family:"Barlow Semi Condensed",sans-serif;font-weight:600;font-size:10.5px;white-space:nowrap}
  .contact-item{display:flex;align-items:center;gap:4px}
  .contact-dot{width:12px;height:12px;border:1.5px solid #fff;border-radius:50%}

  /* back */
  .back-shapes{left:0;top:0;width:530px;height:200px}
  .intro{left:50px;top:26px;width:430px;text-align:center;color:#fff;font-size:10.5px;line-height:1.35}
  .section-title{left:0;top:150px;width:100%;text-align:center;color:var(--sky);font-family:"Barlow Semi Condensed",sans-serif;font-weight:800;font-size:24px;letter-spacing:.4px}
  .body-copy{left:40px;top:186px;width:450px;text-align:center;color:var(--ink);font-size:11px;line-height:1.4}
  .body-copy p+p{margin-top:10px}
  .rsvp{left:0;top:330px;width:100%;text-align:center;color:var(--ink);font-size:12.5px;font-weight:500}
  .photo-round--d{left:40px;top:398px;width:138px;height:138px;background:linear-gradient(160deg,#9aa3ab,#4b4c55)}
  .photo-round--e{left:180px;top:366px;width:170px;height:170px;background:linear-gradient(160deg,#e9d9cf,#7a5236);z-index:2}
  .photo-round--f{left:350px;top:390px;width:138px;height:138px;background:linear-gradient(160deg,#c4b8b0,#5d4f52)}
  .link-box{left:70px;top:590px;width:390px;height:44px;border:2px solid var(--ink);border-top:none}
  .link-box::before,.link-box::after{content:"";position:absolute;top:0;height:2px;background:var(--ink)}
  .link-box::before{left:0;width:50px}
  .link-box::after{right:0;width:50px}
  .link-label{left:0;top:-8px;width:100%;text-align:center;color:var(--ink);font-size:10.5px;font-weight:500}
  .link-url{left:0;top:13px;width:100%;text-align:center;color:var(--ink);font-size:17px;font-weight:600}
</style>
</head>
<body>

<section class="sheet sheet--front" aria-label="Flyer front">
  <div class="abs photo photo-crowd" role="img" aria-label="Group photo of teen participants gathered in a hall"></div>

  <svg class="abs front-base" viewBox="0 0 530 686" aria-hidden="true">
    <path d="M0 455 C140 420 360 422 530 462 V686 H0 Z" fill="var(--slate)"/>
    <path d="M0 455 C140 420 360 422 530 462" fill="none" stroke="#ffffff" stroke-width="5"/>
    <path d="M0 182 H530 V176 H0 Z" fill="#ffffff"/>
  </svg>

  <div class="abs header-band">CROSSPATH TEEN ASSEMBLY OF BRAMBLE VALLEY'S</div>
  <div class="abs brand-mark">Crosspath Teen Assembly of Bramble Valley</div>
  <div class="abs title-block">
    <div class="title-annual">15TH ANNUAL</div>
    <div class="title-event">UNITY SUMMIT &amp; FAIR</div>
    <div class="title-tag">TEENS EXPRESSING THEIR FAITH THROUGH</div>
    <div class="title-media">ART, MUSIC, &amp; DIALOGUE</div>
  </div>

  <div class="abs photo-round photo-round--a" role="img" aria-label="Photo of students standing together outdoors"></div>
  <div class="abs photo-round photo-round--b" role="img" aria-label="Photo of a discussion table with students"></div>
  <div class="abs photo-round photo-round--c" role="img" aria-label="Photo of a dancer performing in traditional dress"></div>

  <div class="abs theme">“Threads of Belief”</div>
  <div class="abs date-row">
    <span class="date-pill">Sunday, March 10th, 2019</span>
    <span class="time-pill">1:30pm-6:30pm</span>
  </div>
  <div class="abs venue">The Fellowship Hall of Saint Quillan Meadows</div>
  <div class="abs address">4870 Larkspur Hollow Road Larkspur Falls, BV 00412</div>
  <div class="abs contact-box">
    <span class="contact-item">
      <svg width="13" height="13" viewBox="0 0 14 14" aria-hidden="true"><circle cx="7" cy="7" r="6.2" fill="none" stroke="#fff" stroke-width="1.3"/><rect x="3.5" y="4.8" width="7" height="4.6" fill="none" stroke="#fff" stroke-width="1"/><path d="M3.5 4.8 L7 7.6 L10.5 4.8" fill="none" stroke="#fff" stroke-width="1"/></svg>
      ctabvgroup@mailbox.example
    </span>
    <span class="contact-item"><span class="contact-dot"></span>CTABV.example</span>
    <span class="contact-item"><span class="contact-dot"></span>Crosspath Teen Assembly of Bramble Valley</span>
  </div>
</section>

<section class="sheet sheet--back" aria-label="Flyer back">
  <svg class="abs back-shapes" viewBox="0 0 530 200" aria-hidden="true">
    <path d="M0 0 H530 V128 C380 92 170 96 0 134 Z" fill="var(--slate)"/>
    <path d="M0 134 C170 96 380 92 530 128 V138 C380 104 170 108 0 146 Z" fill="var(--teal)"/>
  </svg>
  <p class="abs intro">All high school age faith groups are invited to come and join with 150 to 175 other high school students from various faith traditions to participate in the Crosspath Teen Assembly of Bramble Valley's Annual Crosspath Teen Gathering. More than ever, our county and the world needs young leaders who are willing to learn from each other and build stronger communities!</p>

  <h2 class="abs section-title">UNITY SUMMIT</h2>
  <div class="abs body-copy">
    <p>The purpose of this Crosspath Teen Gathering is to bring together young people from diverse ethnic, cultural, and religious backgrounds, and to engage them in dialogue. True dialogue is a conversation on a common subject between two or more persons of differing points of view and/or backgrounds. We feel that this commitment to dialogue will affect relationships in a constructive way in our places of worship and in our community.</p>
    <p>The forum itself involves having eight religiously diverse high school-age students, one adult, and youth leader around each table to discuss common questions. Our youth leaders act as facilitators, but it is stressed that it is the students we want to hear from.</p>
  </div>
  <p class="abs rsvp">RSVP for our UNITY SUMMIT before February 25th, 2019</p>

  <div class="abs photo-round photo-round--d" role="img" aria-label="Photo of students seated at forum tables"></div>
  <div class="abs photo-round photo-round--e" role="img" aria-label="Photo of a student playing taiko drums"></div>
  <div class="abs photo-round photo-round--f" role="img" aria-label="Photo of students playing music"></div>

  <div class="abs link-box">
    <span class="abs link-label">FORUM QUESTIONS Available online at</span>
    <span class="abs link-url">http://ctabv.example/home/unity-fair/</span>
  </div>
</section>

</body>
</html>
```